The Visual Personality of Miss Cobbler Food Trailer

Something that stands out with color and our logo. This is a food trailer that attends several events in the spring and summer. We are known for being one of the best Gumbo producers in mid Michigan. We have been responsible for connecting different communities and cultures together and we are strong supporters of our veterans since this is a veteran owned business. All of our vegetables are fresh and locally purchased. These recipes are originally from New Orleans Louisiana. Our website is Misscobbler.net. This will be used for an 8" x 11" poster. Leave a box or area that states "WHERE WE WILL BE:" so that we can add the location of the event that we are attending.

Target Market(s)

We do cuisine that is recognized in the southern states of the USA. but live in the northern part of the USA. We are providing a menu of different southern recipes so they do not have to go all the way down south for get..

Industry/Entity Type

Food/Restaurant Industry

Font styles to use
Serif
Decorative

Colors
0094D4
00A9DD
6FCCEA
C7EBF8
E9F6FB
59FF00
82FF00
B8FF75
E3FFCB
F4FFEA
FFF300
FFF600
FEFA6F
FFFEC7
FFFEE8
EE7325
F08F49
F5BC92
FAE3D3
FDF4ED
EB3D1F
EC4F4E
F09395
F8D3D4
FCEDEE
A7469A
B969AE
D3A5CF
EDDBEB
F8F0F9

Requirements
Must have
• Our logo, which is "Miss Cobbler", "Homemade Deliciousness". We need an area on the poster where we can manually add the location of the event we will be attending because it changes weekly. location
Nice to have
• Bold colors and logo

```html
<!DOCTYPE html>
<html lang="en">
<head>
<meta charset="utf-8">
<title>Miss Cobbler Food Trailer — Poster</title>
<link rel="stylesheet" href="https://fonts.googleapis.com/css2?family=Arima:wght@500;700&family=Dancing+Script:wght@500&family=Raleway:wght@500;600&display=swap">
<style>
  :root {
    --red: #e52b14;
    --red-deep: #d91e0e;
    --orange: #f58a1f;
    --orange-light: #f7a12b;
    --orange-ring: #f26a1b;
    --white: #ffffff;
    --ink-red: #e3131f;
    --pink: #f09395;
    --photo-bread: #c97a45;
    --photo-board: #5a4633;
    --photo-gumbo: #c2583a;
    --photo-pizza: #d9c7a8;
    --green: #8cc63f;
    --pepper: #ee7325;
  }
  html, body {
    margin: 0;
    padding: 0;
    width: 848px;
    height: 1200px;
    overflow: hidden;
    background: #ffffff;
  }
  .poster {
    position: relative;
    width: 848px;
    height: 1200px;
    overflow: hidden;
    background: linear-gradient(180deg, var(--orange-light) 40%, var(--orange) 80%, var(--orange-ring) 100%);
  }
  .poster__backdrop {
    position: absolute;
    inset: 0;
    width: 848px;
    height: 1200px;
  }
  .logo {
    position: absolute;
    left: 52px;
    top: 67px;
    width: 234px;
    height: 234px;
    border-radius: 50%;
    background: var(--orange-ring);
    opacity: 1;
    display: flex;
    align-items: center;
    justify-content: center;
    box-shadow: 0 0 0 6px rgba(255,120,60,0.35);
  }
  .logo__disc {
    width: 208px;
    height: 208px;
    border-radius: 50%;
    background: var(--white);
    display: flex;
    flex-direction: column;
    align-items: center;
    justify-content: center;
    text-align: center;
  }
  .logo__name {
    font-family: "Arima", serif;
    font-weight: 700;
    font-size: 30px;
    line-height: 1.05;
    color: var(--red-deep);
    letter-spacing: 1px;
  }
  .logo__tagline {
    margin-top: 8px;
    font-family: "Arima", serif;
    font-weight: 700;
    font-size: 11px;
    color: var(--red-deep);
    letter-spacing: 0.5px;
  }
  .photo {
    position: absolute;
  }
  .photo--sandwich {
    left: 440px;
    top: 0;
    width: 408px;
    height: 680px;
  }
  .photo--round {
    border-radius: 50%;
    border: 8px solid var(--white);
    box-shadow: 0 0 0 7px var(--red);
  }
  .photo--gumbo {
    left: -20px;
    top: 530px;
    width: 240px;
    height: 240px;
    background: radial-gradient(circle at 50% 50%, var(--photo-gumbo) 55%, #e9e4de 58%);
  }
  .photo--pizza {
    left: 667px;
    top: 727px;
    width: 182px;
    height: 182px;
    background: radial-gradient(circle at 45% 45%, #e8b59a, var(--photo-pizza) 70%);
  }
  .garnish {
    position: absolute;
  }
  .garnish--cilantro {
    left: 288px;
    top: 652px;
    width: 132px;
    height: 60px;
    border-radius: 30px;
    background: linear-gradient(90deg, #4f9a32, #6fb23f);
    opacity: 0.85;
  }
  .garnish--peppers {
    left: 20px;
    top: 852px;
    width: 132px;
    height: 80px;
    border-radius: 40px;
    background: linear-gradient(160deg, var(--red) 30%, var(--pepper) 70%);
  }
  .garnish--pepper-rings {
    left: 598px;
    top: 1002px;
    width: 92px;
    height: 92px;
    border-radius: 50%;
    background: radial-gradient(circle, #e3ffcb 40%, var(--green) 75%);
  }
  .headline {
    position: absolute;
    left: 260px;
    top: 700px;
    width: 400px;
    text-align: center;
    margin: 0;
    font-family: "Dancing Script", cursive;
    font-weight: 500;
    font-size: 62px;
    line-height: 58px;
    color: var(--ink-red);
  }
  .subline {
    position: absolute;
    left: 240px;
    top: 873px;
    width: 440px;
    text-align: center;
    margin: 0;
    font-family: "Arima", serif;
    font-weight: 700;
    font-size: 22px;
    line-height: 26px;
    letter-spacing: 2px;
    color: var(--white);
  }
  .website {
    position: absolute;
    left: 240px;
    top: 982px;
    width: 440px;
    text-align: center;
    margin: 0;
    font-family: "Arima", serif;
    font-weight: 700;
    font-size: 22px;
    color: var(--white);
  }
  .location {
    position: absolute;
    left: 30px;
    top: 1030px;
    width: 790px;
    height: 152px;
    border-radius: 76px;
    background: rgba(242, 106, 27, 0.75);
    display: flex;
    align-items: center;
    justify-content: center;
  }
  .location__box {
    width: 768px;
    height: 128px;
    border-radius: 64px;
    background: var(--white);
    display: flex;
    flex-direction: column;
    align-items: center;
    justify-content: center;
    gap: 10px;
  }
  .location__label {
    font-family: "Raleway", sans-serif;
    font-weight: 600;
    font-size: 22px;
    color: var(--ink-red);
  }
  .location__address {
    font-family: "Raleway", sans-serif;
    font-weight: 500;
    font-size: 22px;
    color: var(--pink);
  }
</style>
</head>
<body>
  <main class="poster">
    <svg class="poster__backdrop" viewBox="0 0 848 1200" aria-hidden="true">
      <defs>
        <linearGradient id="top-band" x1="0" y1="0" x2="0" y2="1">
          <stop offset="0" stop-color="#ea3f1c"/>
          <stop offset="1" stop-color="#e0260f"/>
        </linearGradient>
      </defs>
      <path d="M0 0 H848 V560 C700 600 520 560 420 520 C280 470 120 420 0 330 Z" fill="url(#top-band)"/>
      <path d="M0 345 C110 430 260 485 390 530 C470 560 560 575 640 560 C520 585 420 575 330 545 C200 505 90 450 0 390 Z" fill="#ffffff"/>
      <path d="M0 392 C90 452 200 507 330 547 C250 540 150 500 0 430 Z" fill="#e52b14"/>
      <circle cx="652" cy="622" r="30" fill="none" stroke="#e52b14" stroke-width="2"/>
      <circle cx="628" cy="636" r="26" fill="none" stroke="#e52b14" stroke-width="1.5"/>
    </svg>

    <div class="logo">
      <div class="logo__disc">
        <div class="logo__name">MISS<br>COBBLER</div>
        <div class="logo__tagline">HOMEMADE DELICIOUSNESS!</div>
      </div>
    </div>

    <svg class="photo photo--sandwich" viewBox="0 0 408 680" role="img" aria-label="Photo of a fried shrimp po'boy with tomato, lettuce, pickles and remoulade on a wooden board">
      <defs>
        <linearGradient id="sandwich-tone" x1="0" y1="0" x2="1" y2="1">
          <stop offset="0" stop-color="#d48a55"/>
          <stop offset="0.55" stop-color="#c97a45"/>
          <stop offset="1" stop-color="#5a4633"/>
        </linearGradient>
      </defs>
      <path d="M60 160 C120 40 260 0 408 0 V540 C350 600 300 660 260 676 C200 690 140 650 80 560 C30 490 -10 440 5 380 C20 320 40 220 60 160 Z" fill="url(#sandwich-tone)"/>
    </svg>

    <div class="photo photo--round photo--gumbo" role="img" aria-label="Photo of a bowl of gumbo with okra, tomato and rice"></div>
    <div class="photo photo--round photo--pizza" role="img" aria-label="Photo of shrimp flatbread topped with tomato and spinach"></div>

    <div class="garnish garnish--cilantro" role="img" aria-label="Cilantro leaves"></div>
    <div class="garnish garnish--peppers" role="img" aria-label="Red and orange chili peppers"></div>
    <div class="garnish garnish--pepper-rings" role="img" aria-label="Green bell pepper rings"></div>

    <h1 class="headline">Homemade<br>Deliciousness</h1>
    <p class="subline">created from fresh and<br>authentic ingredients</p>
    <p class="website">www.misscobbler.net</p>

    <section class="location">
      <div class="location__box">
        <span class="location__label">Where we will be</span>
        <span class="location__address">Your Address here</span>
      </div>
    </section>
  </main>
</body>
</html>
```